Senior Care and Care home flyer

We are getting ready to advertise with a company called "CoupDeal" and our advertisement includes a 3"x8" DOUBLE SIDED insert. Live Area: This is the maximum size of your page content. (Coupon: 3" x 7.9167")
Both sides should have
Address: 3487 Moanalua Rd. Suite 215 Honolulu, HI 96819
Phone: 808-555-0172
Website: www.BrantleyCare.example
-We would like a space for a QR code on both sides

1 side : make color scheme that blue from the last one
Brantley Care Group: featuring Brantley Senior Living
Logo for Senior Living
Brantley Care Group can provide care to your loved ones in our home-Brantley Senior Living Kailua. Clients and their families can experience Brantley's culture of heart-centered, compassionate care in their own home... or in ours.
Senior Living Benefits/Features:
19 Fully Furnished Suites
Meals, Laundry, Housekeeping
Activities & Transportation
On-site 24/7 Care Services
Some items to include on flyer.
Schedule Tour today

Side 2: make the color scheme that green from the last flyer
Brantley Care Group: Featuring Brantley Homecare
Logo for HomeCare
General information for Brantley Care group:
Brantley Care Group has been providing homecare to Oahu's Kupuna for the past 26 years. Brantley Homecare offers personal care services to meet your loved one's needs in the comfort and safety of their own home.
Homecare Services:
Home Health Aides
Skilled Nursing
Bath & Meal Service
Medication Management
Services Available 24/7

Target Market for Side 2: Ages 55-105 Males and Females, looking for care or a home for themselves or their loved ones
-Complimentary Care Consultation
Maybe homecare side says in your home and senior living side said or ours.
Include on both sides
-25+ Years in business
-Locally owned and operated
-Licensed and Insured

Flyer should be 3"x8" DOUBLE SIDED horizontal/landscape/please utilize information that you have used on past ads as a guide.

Industry/Entity Type

Home Health Care Senior Living

Colors
0094D4
00A9DD
6FCCEA
C7EBF8
E9F6FB
00AB8E
00BBA5
67D7C9
C6EFE9
E9F9F6

Requirements
Must have
• Live Area: This is the maximum size of your page content. (Coupon: 3" x 7.9167")
Should not have
• NO PINK OR PEACH colors

```html
<!DOCTYPE html>
<html lang="en">
<head>
<meta charset="utf-8">
<title>Brantley Care Group – Insert</title>
<link href="https://fonts.googleapis.com/css2?family=Open+Sans:wght@400;700&family=Roboto+Condensed:wght@400;700&display=swap" rel="stylesheet">
<style>
:root{
  --page:#6b6a6b;
  --blue-dark:#0e5a6e;
  --blue-mid:#1c8ea6;
  --blue-light:#35b3c8;
  --blue-cta:#3cc0d2;
  --green-dark:#0c5128;
  --green-mid:#1b8f3e;
  --green-light:#2bb54f;
  --green-cta:#26a046;
  --white:#ffffff;
  --ink:#1e1e1e;
  --qr:#c4c4c4;
}
*{box-sizing:border-box;margin:0;padding:0}
html,body{width:1200px;height:935px;overflow:hidden;background:var(--page)}
body{position:relative;font-family:"Open Sans",sans-serif}
.insert{position:absolute;left:24px;width:1147px;height:430px;overflow:hidden;background:#f7f2ea}
.insert--senior{top:24px}
.insert--home{top:480px}
.insert__panel{position:absolute;left:0;top:0;width:736px;height:430px}
.insert--senior .insert__panel{background:linear-gradient(100deg,var(--blue-dark) 0%,var(--blue-mid) 55%,var(--blue-light) 100%)}
.insert--home .insert__panel{background:linear-gradient(100deg,var(--green-dark) 0%,var(--green-mid) 55%,var(--green-light) 100%)}
.insert__backdrop{position:absolute;left:736px;top:0;width:411px;height:430px}
.insert--senior .insert__backdrop{background:linear-gradient(135deg,#f8f5ef 0%,#e3eef2 45%,#f7f2ea 100%)}
.insert--home .insert__backdrop{background:linear-gradient(135deg,#f8f5ef 0%,#e6efe4 45%,#f7f2ea 100%)}
.insert__cta{position:absolute;left:0;top:343px;width:720px;height:61px;
  background:linear-gradient(90deg,var(--white) 0%,var(--white) 72%,rgba(255,255,255,0) 100%)}
.insert__cta span{position:absolute;left:25px;top:5px;font-weight:700;font-size:45px;line-height:52px;white-space:nowrap}
.insert--senior .insert__cta span{color:var(--blue-cta)}
.insert--home .insert__cta span{color:var(--green-cta)}
.insert__photo{position:absolute;left:541px;top:48px;width:338px;height:338px;border-radius:50%}
.insert--senior .insert__photo{background:radial-gradient(circle at 45% 40%,#e8d9cc 0%,#9bb8cf 55%,#5a86b0 100%)}
.insert--home .insert__photo{background:radial-gradient(circle at 50% 40%,#e9e0c4 0%,#b69b72 55%,#6e5a44 100%)}
.insert__title{position:absolute;left:35px;top:27px;color:var(--white);font-weight:700;font-size:50px;line-height:1;white-space:nowrap}
.insert__subtitle{position:absolute;left:35px;top:80px;color:var(--white);font-weight:700;font-size:27px;line-height:1;white-space:nowrap}
.insert__intro{position:absolute;left:36px;top:114px;width:525px;color:var(--white);font-size:15px;line-height:20px}
.insert--home .insert__intro{width:540px}
.insert__heading{position:absolute;left:34px;top:208px;color:var(--white);font-weight:700;font-size:26px;line-height:1;white-space:nowrap}
.insert--home .insert__heading{top:183px}
.features{position:absolute;left:34px;top:244px;list-style:none}
.insert--home .features{top:217px}
.features li{display:flex;align-items:center;height:22px;color:var(--white);font-size:16px;white-space:nowrap}
.features svg{width:22px;height:18px;margin-right:12px;flex:none}
.insert__badges{position:absolute;left:36px;top:409px;color:var(--white);font-size:12.5px;line-height:16px;font-weight:700;white-space:nowrap}
.brand{position:absolute;left:860px;top:28px;display:flex;align-items:center;gap:12px}
.brand__mark{width:46px;height:46px}
.insert--senior .brand__mark{background:var(--blue-cta)}
.insert--home .brand__mark{background:var(--green-cta)}
.brand__name{font-weight:400;font-size:28px;letter-spacing:1px;white-space:nowrap}
.insert--senior .brand__name{color:var(--blue-cta)}
.insert--home .brand__name{color:var(--green-cta);letter-spacing:6px;font-size:24px}
.qr-space{position:absolute;left:899px;top:104px;width:213px;height:195px;background:var(--qr)}
.contact{position:absolute;right:34px;top:320px;text-align:right;font-family:"Roboto Condensed",sans-serif;font-style:normal;font-size:15.5px;line-height:21.7px;color:var(--ink);white-space:nowrap}
.contact b{font-weight:700}
</style>
</head>
<body>

<section class="insert insert--senior">
  <div class="insert__panel"></div>
  <div class="insert__backdrop" role="img" aria-label="Soft faded photo of a caregiver with a smiling senior"></div>
  <div class="insert__cta"><span>SCHEDULE TOUR TODAY</span></div>
  <div class="insert__photo" role="img" aria-label="Photo of a laughing senior man in a wheelchair with a caregiver in blue scrubs"></div>
  <h1 class="insert__title">BRANTLEY CARE GROUP</h1>
  <h2 class="insert__subtitle">FEATURING BRANTLEY SENIOR LIVING</h2>
  <p class="insert__intro">Brantley Care Group can provide care to your loved ones in our home-Brantley Senior Living Kailua. Clients and their families can experience Brantley's culture of heart centered, compassionate care in their own home... or in ours.</p>
  <h3 class="insert__heading">SENIOR LIVING BENEFITS/FEATURES:</h3>
  <ul class="features">
    <li><svg viewBox="0 0 22 18"><path d="M2 9l6 6L20 2" fill="none" stroke="#fff" stroke-width="4"/></svg>19 Fully Furnished Suites</li>
    <li><svg viewBox="0 0 22 18"><path d="M2 9l6 6L20 2" fill="none" stroke="#fff" stroke-width="4"/></svg>Meals, Laundry, Housekeeping</li>
    <li><svg viewBox="0 0 22 18"><path d="M2 9l6 6L20 2" fill="none" stroke="#fff" stroke-width="4"/></svg>Activities &amp; Transportation</li>
    <li><svg viewBox="0 0 22 18"><path d="M2 9l6 6L20 2" fill="none" stroke="#fff" stroke-width="4"/></svg>On-site 24/7 Care Services</li>
  </ul>
  <p class="insert__badges">25+ Years in Business &nbsp;•&nbsp; Locally Owned &amp; Operated &nbsp;•&nbsp; Licensed &amp; Insured &nbsp;•&nbsp; Complimentary Care Consultation</p>
  <div class="brand"><div class="brand__mark"></div><div class="brand__name">Senior Living</div></div>
  <div class="qr-space"></div>
  <address class="contact">
    <b>ADDRESS:</b> 3487 MOANALUA RD.<br>
    SUITE 215 HONOLULU, HI 96819<br>
    <b>PHONE:</b> 808-555-0172<br>
    <b>WEBSITE:</b> WWW.BRANTLEYCARE.EXAMPLE
  </address>
</section>

<section class="insert insert--home">
  <div class="insert__panel"></div>
  <div class="insert__backdrop" role="img" aria-label="Soft faded photo of a caregiver with a smiling senior"></div>
  <div class="insert__cta"><span>SCHEDULE TOUR TODAY</span></div>
  <div class="insert__photo" role="img" aria-label="Photo of a caregiver helping two seniors exercise with hand weights in a living room"></div>
  <h1 class="insert__title">BRANTLEY CARE GROUP</h1>
  <h2 class="insert__subtitle">FEATURING BRANTLEY HOMECARE</h2>
  <p class="insert__intro">Brantley Care Group has been providing homecare to Oahu's Kupuna for the past 26 years. Brantley Homecare offers personal care services to meet your loved one's needs in the comfort and safety of their own home.</p>
  <h3 class="insert__heading">HOMECARE SERVICES:</h3>
  <ul class="features">
    <li><svg viewBox="0 0 22 18"><path d="M2 9l6 6L20 2" fill="none" stroke="#fff" stroke-width="4"/></svg>Home Health Aides</li>
    <li><svg viewBox="0 0 22 18"><path d="M2 9l6 6L20 2" fill="none" stroke="#fff" stroke-width="4"/></svg>Skilled Nursing</li>
    <li><svg viewBox="0 0 22 18"><path d="M2 9l6 6L20 2" fill="none" stroke="#fff" stroke-width="4"/></svg>Bath &amp; Meal Service</li>
    <li><svg viewBox="0 0 22 18"><path d="M2 9l6 6L20 2" fill="none" stroke="#fff" stroke-width="4"/></svg>Medication Management</li>
    <li><svg viewBox="0 0 22 18"><path d="M2 9l6 6L20 2" fill="none" stroke="#fff" stroke-width="4"/></svg>Services Available 24/7</li>
  </ul>
  <p class="insert__badges">25+ Years in Business &nbsp;•&nbsp; Locally Owned &amp; Operated &nbsp;•&nbsp; Licensed &amp; Insured &nbsp;•&nbsp; Complimentary Care Consultation</p>
  <div class="brand"><div class="brand__mark"></div><div class="brand__name">HOMECARE</div></div>
  <div class="qr-space"></div>
  <address class="contact">
    <b>ADDRESS:</b> 3487 MOANALUA RD.<br>
    SUITE 215 HONOLULU, HI 96819<br>
    <b>PHONE:</b> 808-555-0172<br>
    <b>WEBSITE:</b> WWW.BRANTLEYCARE.EXAMPLE
  </address>
</section>

</body>
</html>
```